Half page (a5) ad for a company

I need a design for an ad for a company to be published in a conference catalogue. Please find enclosed the logo for a company. The company is providing health screening services. Ad should be subtle and minimalistic, i.e. logo in the centre and a phrase saying: "Be in charge of your own health" and the website bluefen.co.uk. Also please find enclosed guidlines for colours and fonts to be used.

```html
<!DOCTYPE html>
<html lang="en">
<head>
<meta charset="utf-8">
<title>Bluefen Private – Advert</title>
<link rel="stylesheet" href="https://fonts.googleapis.com/css2?family=Montserrat:wght@400;700&display=swap">
<style>
  :root {
    --ink: #000000;
    --paper: #ffffff;
    --brand-red: #e41f26;
    --brand-red-deep: #8c0a1e;
  }
  * { margin: 0; padding: 0; box-sizing: border-box; }
  html, body { width: 849px; height: 1200px; overflow: hidden; background: var(--paper); }
  .ad {
    position: relative;
    width: 849px;
    height: 1200px;
    background: var(--paper);
    font-family: "Montserrat", Arial, sans-serif;
  }
  .ad__header-shape {
    position: absolute;
    top: 0;
    left: 0;
    width: 849px;
    height: 880px;
    display: block;
  }
  .ad__brand-mark {
    position: absolute;
    top: 232px;
    left: 334px;
    width: 180px;
    height: 180px;
    border-radius: 50%;
    background: var(--brand-red);
  }
  .ad__brand-name {
    position: absolute;
    top: 520px;
    left: 0;
    width: 100%;
    text-align: center;
    color: var(--brand-red);
    font-weight: 400;
    font-size: 80px;
    line-height: 1;
    white-space: nowrap;
  }
  .ad__tagline {
    position: absolute;
    top: 950px;
    left: 0;
    width: 100%;
    text-align: center;
    color: var(--ink);
    font-weight: 700;
    font-size: 45px;
    line-height: 1.2;
    white-space: nowrap;
  }
  .ad__website {
    position: absolute;
    top: 1025px;
    left: 0;
    width: 100%;
    text-align: center;
    color: var(--brand-red);
    font-weight: 400;
    font-size: 28px;
    line-height: 1.2;
  }
</style>
</head>
<body>
  <main class="ad">
    <svg class="ad__header-shape" viewBox="0 0 849 880" aria-hidden="true">
      <defs>
        <linearGradient id="sweepGradient" x1="0" y1="0" x2="1" y2="0">
          <stop offset="0" style="stop-color:#8c0a1e"/>
          <stop offset="0.55" style="stop-color:#e41f26"/>
          <stop offset="1" style="stop-color:#e41f26"/>
        </linearGradient>
      </defs>
      <path class="ad__red-sweep" fill="url(#sweepGradient)"
            d="M0,598 C190,830 330,866 430,866 C570,866 700,790 849,598 L849,0 L0,0 Z"/>
      <path class="ad__black-field" fill="#000000"
            d="M0,0 H849 V601 C680,790 530,829 425,829 C320,829 180,800 0,600 Z"/>
    </svg>

    <div class="ad__brand-mark" role="img" aria-label="Bluefen Private brand mark"></div>
    <h1 class="ad__brand-name">Bluefen Private</h1>

    <p class="ad__tagline">Be in charge of your own health</p>
    <p class="ad__website">bluefen.co.uk</p>
  </main>
</body>
</html>
```